Business Card Design

Our Pharmacy Opens late - the last to close in Brisbane
over 30 years since opened.
Open from 7am - 11pm every day.
Next to Corbel 7 Day Medical Centre
Parking in front of shop
Sit with a pharmacist for every script - the best advice every time.
Private consulting room.
We have the medication that you need.
Wide range Home Health Care products.

Looking for a card that my (young) staff feel happy to hand out to people they they meet.
Updates

Hello Many thanks for your submissions I just need to clarify the costings for this project as per my updated brief Please confirm then we can proceed Many thanks Clive

Reason: due to the adjusted brief and query I have extended the deadline Many thanks for those that have submitted, I will choose the designer as soon as I understand the costings of the project, as per the message despatched today Regards clive

Target Market(s)

men and women 30-70

Industry/Entity Type

Business

Contact Information for Business Card

Meltons Pharmacy - Corbel
317 Galloway Rd
Corbel 4187
Last to Close
Open 7am - 11pm

Font styles to use
Sans Serif

Requirements
Must have
• each batch of 250 will have the following staff names

Doreen Vallow, Senior Pharmacist
Lucia Tomba, Pharmacist
Wu Lan, Pharmacist
Odalie Brunskill, Pharmacist
Greta Lounds, Retail Manager
Joy Mettrick, Marketing Manager
Clive Melton, Pharmacist Proprietor
Should not have
• Please advise if the cost of this job covers the 7 individualised business cards.

Each staff member needs their own card.

please advise

```html
<!DOCTYPE html>
<html lang="en">
<head>
<meta charset="utf-8">
<title>Meltons Pharmacy – Business Card</title>
<link href="https://fonts.googleapis.com/css2?family=Open+Sans:wght@400;600;700&display=swap" rel="stylesheet">
<style>
  :root {
    --page: #eeeae3;
    --card-white: #ffffff;
    --yellow: #e4e22c;
    --yellow-light: #f3f27a;
    --navy: #2a2f7a;
    --blue-soft: #8b8fd0;
    --ink: #333333;
    --title-blue: #5a63c9;
  }
  html, body {
    margin: 0;
    width: 1200px;
    height: 1019px;
    overflow: hidden;
    background: var(--page);
    font-family: "Open Sans", Arial, sans-serif;
  }
  .card {
    position: absolute;
    left: 250px;
    width: 700px;
    height: 400px;
    overflow: hidden;
    box-shadow: 0 6px 18px rgba(0,0,0,0.18);
  }
  .card-front { top: 90px; background: var(--card-white); }
  .card-back { top: 530px; background: linear-gradient(135deg, var(--yellow-light), var(--yellow)); }
  .swoosh { position: absolute; inset: 0; }
  .brand {
    position: absolute;
    left: 40px;
    top: 140px;
    display: flex;
    align-items: center;
    gap: 12px;
  }
  .brand-dot {
    width: 28px;
    height: 28px;
    border-radius: 50%;
    background: var(--yellow);
  }
  .brand-name {
    font-size: 26px;
    font-weight: 700;
    color: var(--navy);
    line-height: 1.15;
  }
  .details {
    position: absolute;
    left: 290px;
    top: 34px;
    color: var(--ink);
  }
  .person-name { font-size: 21px; font-weight: 700; margin: 0; line-height: 1.3; }
  .person-title { font-size: 13px; color: var(--title-blue); margin: 0 0 16px; }
  .address { font-size: 14px; font-weight: 700; line-height: 1.4; margin: 0 0 10px; }
  .contact-list { list-style: none; margin: 0; padding: 0; font-size: 13px; }
  .contact-list li { display: flex; align-items: center; gap: 10px; height: 22px; }
  .contact-icon { width: 13px; height: 13px; fill: var(--navy); }
  .back-panel {
    position: absolute;
    left: 400px;
    top: 110px;
    width: 200px;
    height: 180px;
    background: linear-gradient(160deg, #ffffff, #e6e6e6);
  }
</style>
</head>
<body>
  <section class="card card-front">
    <svg class="swoosh" viewBox="0 0 700 400" aria-hidden="true">
      <path d="M0 318 C300 318 515 290 700 76 L700 90 C520 300 300 330 0 330 Z" fill="var(--yellow-light)"/>
      <path d="M0 330 C300 330 520 300 700 90 L700 400 L0 400 Z" fill="var(--yellow)"/>
      <path d="M580 212 C630 170 668 126 700 84" fill="none" stroke="var(--navy)" stroke-width="7"/>
      <path d="M530 262 C565 248 592 230 612 210" fill="none" stroke="var(--blue-soft)" stroke-width="5" stroke-linecap="round"/>
    </svg>

    <div class="brand">
      <span class="brand-dot"></span>
      <span class="brand-name">Meltons<br>Pharmacy</span>
    </div>

    <div class="details">
      <p class="person-name">Clive Melton</p>
      <p class="person-title">Pharmacist Proprietor</p>
      <p class="address">317 Galloway Rd, Corbel 4187<br>Open 7am - 11pm</p>
      <ul class="contact-list">
        <li><svg class="contact-icon" viewBox="0 0 16 16"><path d="M3 1h3l1 4-2 1a9 9 0 0 0 5 5l1-2 4 1v3a2 2 0 0 1-2 2A13 13 0 0 1 1 3a2 2 0 0 1 2-2z"/></svg>(012) 555 0147</li>
        <li><svg class="contact-icon" viewBox="0 0 16 16"><path d="M4 0h8a1 1 0 0 1 1 1v14a1 1 0 0 1-1 1H4a1 1 0 0 1-1-1V1a1 1 0 0 1 1-1zm0 2v11h8V2z"/></svg>(012) 555 0147</li>
        <li><svg class="contact-icon" viewBox="0 0 16 16"><path d="M4 0h7v4H4zM1 5h14v8h-3v3H4v-3H1zm4 5v4h6v-4z"/></svg>(012) 555 0147</li>
        <li><svg class="contact-icon" viewBox="0 0 16 16"><path d="M0 3h16v10H0zm1 1v.5l7 5 7-5V4z"/></svg>clive@meltonsrx.com</li>
      </ul>
    </div>
  </section>

  <section class="card card-back">
    <div class="back-panel"></div>
  </section>
</body>
</html>
```